Scrum Master & Agile IT Coach Needing Business Website

Hello, my name is Joel Brandt
I am a project manger, scrum master, & agile coach. I work with IT development teams on major projects for Summit 300 companies . My project management business has a website and can be found here: www.tk-steadfast.example

I have launched a new company, ALL focused on IT Agile Coaching, I am looking to have a website created for my new company - the name of the new company is: Q's and V's - Agile IT Coaching and Training.
I have a logo and it is provided in the materials. I like to logo; I am open to different color pallets.

The website will have a total of 7 pages; I have content for 5 of the 7 pages prepared; the other 2 pages will say under construction.

Page 1 Who am I, What I do, My Experience
Demonstrated experience and progression from Scrum Master to
Program Manager to Coach

Page 2 Q's & V's - Agile Team Coaching
teams working major IT projects, multiple months/years

Page 3 Coaching @ the Team Level

Page 4 Coaching @ the Program Level ; LIMBr ART level

Pages 5 -6 Under Construction

Page 7 Presentations, Slide Decks, Reference Materials

Mentors Nook need to have this highlighted somewhere Monthly Blog
Updates

Industry/Entity Type

IT development

Coding

Coded - Design and coding required

Number of Pages Required

5+ page

Requirements
Must have
• the website must be bold - I want those who visit to remember coming to my coaching site
Nice to have
• nice to have will be a modern / futuristic website; I work with IT developers, I want a website they will like
Should not have
• should not be stiff - it should be professional but fun

```html
<!DOCTYPE html>
<html lang="en">
<head>
<meta charset="UTF-8">
<title>Q's &amp; V's – Agile IT Coaching &amp; Training</title>
<link rel="stylesheet" href="https://fonts.googleapis.com/css2?family=Jost:wght@400;500&family=Roboto+Condensed:wght@400;700&family=Roboto:wght@400;500&display=swap">
<style>
:root{
  --navy:#0b3f6a;
  --navy-deep:#0a3358;
  --navy-text:#0d3d66;
  --white:#ffffff;
  --ink:#1d2430;
  --muted:#3a4350;
  --footer-bg:#f1f3f7;
  --rule:#2b3440;
  --card-a:#1f4f7d;
  --card-b:#4f7ca6;
}
*{margin:0;padding:0;box-sizing:border-box}
html,body{width:1200px;height:2841px;overflow:hidden}
body{position:relative;background:var(--white);font-family:"Roboto Condensed",sans-serif;color:var(--ink)}
.abs{position:absolute}

/* hero */
.hero{left:0;top:0;width:1200px;height:666px;background:linear-gradient(180deg,#2d5278 0%,#34628e 45%,#1f4f7e 100%)}
.logo{display:flex;align-items:center;gap:10px;font-family:"Jost",sans-serif;font-weight:500;font-size:28px;color:var(--white)}
.logo .mark{width:26px;height:26px;border:2px solid currentColor}
.nav{left:417px;top:35px;width:661px;height:45px;background:var(--navy);border-radius:6px;display:flex;align-items:center;justify-content:space-around;padding:0 8px}
.nav a{color:var(--white);text-decoration:none;font-size:15.5px}
.nav a.active{font-weight:700}
.hero-title{left:0;width:1200px;top:448px;text-align:center;font-family:"Jost",sans-serif;font-weight:500;font-size:46px;color:var(--white)}
.hero-sub{left:230px;width:740px;top:510px;text-align:center;font-size:25px;line-height:40px;color:var(--white)}

/* about */
.about{left:0;top:666px;width:1200px;height:834px;background:var(--navy)}
.portrait{left:144px;top:740px;width:335px;height:287px;border-radius:14px;background:linear-gradient(135deg,#b48a5c,#6f6a70 60%,#d6d9de)}
.name{left:144px;width:335px;top:1040px;text-align:center;font-family:"Jost",sans-serif;font-weight:500;font-size:46px;color:var(--white)}
.role{left:130px;width:363px;top:1097px;text-align:center;font-weight:700;font-size:19px;color:var(--white)}
.about-h{left:530px;top:735px;font-family:"Jost",sans-serif;font-weight:500;font-size:44px;color:var(--white)}
.about-p{left:534px;top:808px;width:522px;font-size:15.5px;line-height:27.2px;color:var(--white);text-align:justify;height:218px;overflow:hidden}
.btn{background:var(--white);color:var(--navy-text);font-weight:700;font-size:17px;display:flex;align-items:center;justify-content:center;border-radius:3px}
.read-more{left:534px;top:1056px;width:132px;height:46px}
.badges{left:144px;top:1168px;width:912px;height:120px}
.cert-btn{top:1369px;height:53px;border-radius:8px}

/* what I do */
.section-h{left:0;width:1200px;text-align:center;font-family:"Jost",sans-serif;font-weight:500;font-size:46px;color:var(--navy-text)}
.card{top:1654px;width:215px;height:192px;border-radius:12px;overflow:hidden}
.card .bg{position:absolute;inset:0;background:linear-gradient(160deg,var(--card-a),var(--card-b))}
.card p{position:absolute;inset:0;display:flex;align-items:center;justify-content:center;text-align:center;font-family:"Jost",sans-serif;font-size:21px;line-height:40px;color:var(--white);padding:0 6px}

/* experience */
.panel{left:128px;top:2013px;width:950px;height:482px;background:var(--white);box-shadow:0 2px 10px rgba(0,0,0,.08)}
.tabs{display:flex;height:56px;border-bottom:1px solid #e3e6ea}
.tab{display:flex;align-items:center;justify-content:center;font-family:"Jost",sans-serif;font-size:17px;color:var(--navy-text)}
.tab.on{background:var(--navy);color:var(--white)}
.tab+.tab{border-left:1px solid #c9cfd6}
.list{list-style:none;padding:40px 0 0 32px}
.list li{display:flex;align-items:center;gap:18px;height:48px;font-family:"Jost",sans-serif;font-size:19px;color:var(--ink)}

/* footer */
.footer{left:0;top:2530px;width:1200px;height:311px;background:var(--footer-bg)}
.footer .logo{color:var(--navy)}
.f-text{left:148px;top:2634px;width:215px;font-family:"Roboto",sans-serif;font-size:14.5px;line-height:27px;color:var(--muted);text-align:justify}
.f-col h4{font-weight:700;font-size:18px;color:var(--ink);margin-bottom:6px}
.f-col a{display:block;font-family:"Roboto",sans-serif;font-size:15px;line-height:27px;color:var(--muted);text-decoration:none}
.email{left:766px;top:2611px;width:167px;height:45px;border:1px solid #aab1ba;background:var(--white);font-family:"Roboto",sans-serif;font-size:14px;color:#8a929c;padding:12px 14px}
.subscribe{left:940px;top:2611px;width:112px;height:45px;border-radius:23px;background:var(--navy);color:var(--white);font-family:"Roboto",sans-serif;font-weight:500;font-size:15px;display:flex;align-items:center;justify-content:center}
.social{left:768px;top:2718px;display:flex;gap:14px;font-family:"Roboto",sans-serif;font-size:14px;color:var(--ink)}
.rule{left:0;top:2785px;width:1200px;height:1px;background:var(--rule)}
.copy{left:0;width:1200px;top:2802px;text-align:center;font-family:"Roboto",sans-serif;font-size:12.5px;color:var(--ink)}
</style>
</head>
<body>

<div class="abs hero" role="img" aria-label="Photo of a team collaborating around laptops and charts, tinted navy"></div>
<div class="abs logo" style="left:128px;top:38px"><span class="mark"></span>Q's &amp; V's</div>
<nav class="abs nav">
  <a class="active">Home</a><a>Q's &amp; V's</a><a>Team Level</a><a>Program Level</a><a>Under Construction</a><a>Presentation</a>
</nav>
<h1 class="abs hero-title">Who am I, What I do, My Experience !</h1>
<p class="abs hero-sub">Demonstrate experience and progression from Scrum Master to Program Manager to Coach</p>

<section class="abs about"></section>
<div class="abs portrait" role="img" aria-label="Portrait photo of Joel Brandt"></div>
<h2 class="abs name">Joel Brandt</h2>
<p class="abs role">Senior Scrum Master &amp; Team Agile Coach</p>
<h2 class="abs about-h">Who I am</h2>
<p class="abs about-p">Lorem ipsum dolor sit amet, consectetur adipiscing elit, sed do eiusmod tempor incididunt ut labore et dolore magna aliqua. Quis ipsum suspendisse ultrices gravida. Risus commodo viverra maecenas accumsan lacus vel facilisis. Lorem ipsum dolor sit amet, consectetur adipiscing elit, sed do eiusmod tempor incididunt ut labore et dolore magna aliqua. Quis ipsum suspendisse ultrices gravida. Risus commodo viverra maecenas accumsan lacus vel facilisis. Lorem ipsum dolor sit amet, consectetur adipiscing elit, sed do eiusmod tempor incididunt ut labore et dolore magna aliqua. consectetur adipiscing elit, sed do eiusmod tempor incididunt ut labore et dolore</p>
<div class="abs btn read-more">Read More</div>

<svg class="abs badges" viewBox="0 0 912 120" role="img" aria-label="Certification badges">
  <polygon points="73,4 129,34 129,90 73,118 17,90 17,34" fill="#ffffff" stroke="#1b2c4a" stroke-width="6"/>
  <polygon points="272,2 332,60 272,118 212,60" fill="#ffffff" stroke="#2d3e5a" stroke-width="6"/>
  <circle cx="451" cy="60" r="46" fill="#f3a33a"/>
  <circle cx="451" cy="60" r="32" fill="#f7c26b"/>
  <circle cx="638" cy="60" r="56" fill="#2a8fd6"/>
  <circle cx="638" cy="60" r="40" fill="#1f6fb3"/>
  <circle cx="826" cy="60" r="56" fill="#f2a51e"/>
  <circle cx="826" cy="60" r="40" fill="#e38d10"/>
</svg>

<div class="abs btn cert-btn" style="left:252px;width:168px">Sprint Guild</div>
<div class="abs btn cert-btn" style="left:489px;width:168px">Certvault</div>
<div class="abs btn cert-btn" style="left:725px;width:223px">LIMBr Scaled Agile Alliance</div>

<h2 class="abs section-h" style="top:1565px">What I Do</h2>
<div class="abs card" style="left:144px"><div class="bg" role="img" aria-label="Scrum process imagery"></div><p>Sr. Scrum Master</p></div>
<div class="abs card" style="left:376px"><div class="bg" role="img" aria-label="Scrum roles diagram imagery"></div><p>Advanced LIMBr<br>Scrum Master</p></div>
<div class="abs card" style="left:608px"><div class="bg" role="img" aria-label="Office workspace imagery"></div><p>Hybrid Scrum Master/<br>Project Manager</p></div>
<div class="abs card" style="left:840px"><div class="bg" role="img" aria-label="Business meeting imagery"></div><p>Business<br>(Finance Transformation<br>Program Manager)</p></div>

<h2 class="abs section-h" style="top:1915px">What Is My Experience</h2>
<div class="abs panel">
  <div class="tabs">
    <div class="tab on" style="width:282px">As a LIMBr Adv Scrum Master, I:</div>
    <div class="tab" style="width:356px">As a Hybrid Scrum Master / Project Manager, I:</div>
    <div class="tab" style="width:312px">Business Transformation Program Manager</div>
  </div>
  <ul class="list">
    <li><svg width="38" height="26" viewBox="0 0 38 26"><rect x="8" y="2" width="24" height="16" fill="none" stroke="#2b5d8a" stroke-width="2"/><path d="M2 23h34" stroke="#2b5d8a" stroke-width="2"/><path d="M14 10l4 4 7-7" fill="none" stroke="#2b5d8a" stroke-width="2"/></svg>Stand up teams</li>
    <li><svg width="38" height="26" viewBox="0 0 38 26"><rect x="8" y="2" width="24" height="16" fill="none" stroke="#2b5d8a" stroke-width="2"/><path d="M2 23h34" stroke="#2b5d8a" stroke-width="2"/><path d="M14 10l4 4 7-7" fill="none" stroke="#2b5d8a" stroke-width="2"/></svg>Run development efforts concurrently leading multiple teams</li>
    <li><svg width="38" height="26" viewBox="0 0 38 26"><rect x="8" y="2" width="24" height="16" fill="none" stroke="#2b5d8a" stroke-width="2"/><path d="M2 23h34" stroke="#2b5d8a" stroke-width="2"/><path d="M14 10l4 4 7-7" fill="none" stroke="#2b5d8a" stroke-width="2"/></svg>Run LIMBr ceremonies</li>
    <li><svg width="38" height="26" viewBox="0 0 38 26"><rect x="8" y="2" width="24" height="16" fill="none" stroke="#2b5d8a" stroke-width="2"/><path d="M2 23h34" stroke="#2b5d8a" stroke-width="2"/><path d="M14 10l4 4 7-7" fill="none" stroke="#2b5d8a" stroke-width="2"/></svg>Scrum of Scrums facilitator</li>
    <li><svg width="38" height="26" viewBox="0 0 38 26"><rect x="8" y="2" width="24" height="16" fill="none" stroke="#2b5d8a" stroke-width="2"/><path d="M2 23h34" stroke="#2b5d8a" stroke-width="2"/><path d="M14 10l4 4 7-7" fill="none" stroke="#2b5d8a" stroke-width="2"/></svg>PI Planning team facilitator (multiple teams on ART)</li>
    <li><svg width="38" height="26" viewBox="0 0 38 26"><rect x="8" y="2" width="24" height="16" fill="none" stroke="#2b5d8a" stroke-width="2"/><path d="M2 23h34" stroke="#2b5d8a" stroke-width="2"/><path d="M14 10l4 4 7-7" fill="none" stroke="#2b5d8a" stroke-width="2"/></svg>Teach and coach to advanced development team strategies</li>
    <li><svg width="38" height="26" viewBox="0 0 38 26"><rect x="8" y="2" width="24" height="16" fill="none" stroke="#2b5d8a" stroke-width="2"/><path d="M2 23h34" stroke="#2b5d8a" stroke-width="2"/><path d="M14 10l4 4 7-7" fill="none" stroke="#2b5d8a" stroke-width="2"/></svg>Lead program level communications and business status updates on behalf of the team</li>
  </ul>
</div>

<footer class="abs footer"></footer>
<div class="abs logo" style="left:152px;top:2582px;font-size:26px;color:var(--navy)"><span class="mark"></span>Q's &amp; V's</div>
<p class="abs f-text">Lorem ipsum dolor sit amet, consectetur adipiscing elit, sed do eiusmod tempor incididunt ut labore et dolore magna aliqua.</p>
<div class="abs f-col" style="left:430px;top:2578px"><h4>Quick Links</h4><a>Home</a><a>Q's &amp; V's</a><a>Team Level</a><a>Program Level</a><a>Under Construction</a></div>
<div class="abs f-col" style="left:606px;top:2578px"><h4>Help Links</h4><a>Terms &amp; Conditions</a><a>Presentation</a><a>Privacy</a><a>About Us</a><a>Support</a></div>
<div class="abs f-col" style="left:768px;top:2576px"><h4>Stay Connected</h4></div>
<div class="abs email">Email</div>
<div class="abs subscribe">Subscribe</div>
<div class="abs f-col" style="left:768px;top:2676px"><h4>Follow</h4></div>
<div class="abs social"><span>Loop</span><span>Snap</span><span>Chirp</span></div>
<div class="abs rule"></div>
<p class="abs copy">© copyrights 2022 Q's &amp; V's Agile It Coaching &amp; Training LLC | &nbsp;All Rights Reserved</p>

</body>
</html>
```